Business Card Design

Company is a Commercial Building Company specialising in New Construction and existing refurbishments

Industry/Entity Type

Business

Contact Information for Business Card

Liam Porter
Construction Manager
E Liam@marshbuilding.com.au
M 0400 213 594
Mail 14 Tarrant Rise Larkhaven WA 6208

```html
<!DOCTYPE html>
<html lang="en">
<head>
<meta charset="utf-8">
<title>Marsh Building &amp; Construction — Business Card</title>
<link href="https://fonts.googleapis.com/css2?family=Roboto:wght@300;400;500&display=swap" rel="stylesheet">
<style>
  :root {
    --bg: #e9e6e1;
    --card: #ffffff;
    --navy: #232b45;
    --cyan: #1fb3dc;
    --orange: #f28c1e;
    --ink: #2a2f3a;
    --photo-sky: #a9c9e6;
    --photo-wall: #d8d3b8;
    --photo-lawn: #5f8a3a;
  }
  * { margin: 0; padding: 0; box-sizing: border-box; }
  html, body { width: 1200px; height: 848px; overflow: hidden; }
  body {
    background: var(--bg);
    font-family: "Roboto", Arial, sans-serif;
    position: relative;
  }
  .card {
    position: absolute;
    left: 290px;
    width: 620px;
    height: 354px;
    background: var(--card);
    box-shadow: 0 6px 18px rgba(0,0,0,0.15);
    overflow: hidden;
  }
  .card--front { top: 48px; }
  .card--back { top: 446px; }

  .front-art { position: absolute; inset: 0; }

  .brand {
    position: absolute;
    display: flex;
    align-items: center;
    gap: 8px;
    color: var(--navy);
    font-weight: 500;
    text-transform: uppercase;
    line-height: 1.1;
  }
  .brand__mark { background: var(--cyan); flex: none; }
  .card--front .brand { top: 40px; right: 36px; font-size: 15px; }
  .card--front .brand__mark { width: 14px; height: 14px; }

  .person { position: absolute; top: 128px; right: 36px; text-align: right; }
  .person__name { color: var(--cyan); font-size: 36px; font-weight: 300; line-height: 1; }
  .person__role { color: var(--ink); font-size: 13px; font-weight: 400; margin-top: 4px; }

  .contact {
    position: absolute;
    right: 36px;
    bottom: 34px;
    list-style: none;
    text-align: right;
    color: var(--ink);
    font-size: 15px;
    font-weight: 300;
    line-height: 1.45;
  }
  .contact li { display: flex; justify-content: flex-end; align-items: center; gap: 8px; }
  .contact svg { width: 13px; height: 13px; fill: var(--cyan); flex: none; }

  .back-art { position: absolute; inset: 0; }
  .card--back .brand { left: 150px; top: 200px; font-size: 24px; }
  .card--back .brand__mark { width: 22px; height: 22px; }
</style>
</head>
<body>

  <section class="card card--front">
    <svg class="front-art" width="620" height="354" viewBox="0 0 620 354">
      <defs>
        <linearGradient id="photoTones" x1="0" y1="0" x2="0" y2="1">
          <stop offset="0" stop-color="var(--photo-sky)"/>
          <stop offset="0.45" stop-color="var(--photo-wall)"/>
          <stop offset="0.82" stop-color="#9aa6a8"/>
          <stop offset="1" stop-color="var(--photo-lawn)"/>
        </linearGradient>
      </defs>
      <path role="img" aria-label="Photograph of a modern curved two-storey home with pool"
            d="M0 0 H300 C232 80 222 250 345 354 H0 Z" fill="url(#photoTones)"/>
      <path d="M300 0 C232 80 222 250 345 354" fill="none" stroke="var(--navy)" stroke-width="8"/>
    </svg>

    <div class="brand"><span class="brand__mark"></span><span>Marsh Building<br>&amp; Construction</span></div>

    <div class="person">
      <h1 class="person__name">Liam Porter</h1>
      <p class="person__role">Construction Manager</p>
    </div>

    <ul class="contact">
      <li>0400 213 594
        <svg viewBox="0 0 24 24"><path d="M6.6 10.8a15 15 0 0 0 6.6 6.6l2.2-2.2a1 1 0 0 1 1-.25 11.4 11.4 0 0 0 3.6.57 1 1 0 0 1 1 1V20a1 1 0 0 1-1 1A17 17 0 0 1 3 4a1 1 0 0 1 1-1h3.5a1 1 0 0 1 1 1c0 1.25.2 2.45.57 3.6a1 1 0 0 1-.25 1z"/></svg>
      </li>
      <li>Liam@marshbuilding.com.au
        <svg viewBox="0 0 24 24"><path d="M2 5h20v14H2z M2 5l10 8 10-8" stroke="#fff" stroke-width="1.5"/></svg>
      </li>
      <li>14 Tarrant Rise Larkhaven WA 6208
        <svg viewBox="0 0 24 24"><path d="M12 2a7 7 0 0 0-7 7c0 5.2 7 13 7 13s7-7.8 7-13a7 7 0 0 0-7-7zm0 9.5A2.5 2.5 0 1 1 12 6.5a2.5 2.5 0 0 1 0 5z"/></svg>
      </li>
    </ul>
  </section>

  <section class="card card--back">
    <svg class="back-art" width="620" height="354" viewBox="0 0 620 354">
      <defs>
        <linearGradient id="fadedPhoto" x1="0" y1="0" x2="1" y2="1">
          <stop offset="0" stop-color="#f4f4f2"/>
          <stop offset="0.6" stop-color="#e6e4de"/>
          <stop offset="1" stop-color="#dcdcd8"/>
        </linearGradient>
      </defs>
      <rect role="img" aria-label="Faded photograph of a modern home behind the company name"
            width="620" height="354" fill="url(#fadedPhoto)"/>
    </svg>
    <div class="brand"><span class="brand__mark"></span><span>Marsh Building<br>&amp; Construction</span></div>
  </section>

</body>
</html>
```